Salon and Spa Distributor Business Card

Need a business card. We are are distributor in the salon and spa industry. We identify with natural beauty. Need a card with:
Company Name: Petal Quarry"
Title: "President & CEO"
Address
Company Phone number
email
website
Tag Line:" The Professional Salon Source"

Industry/Entity Type

Business

Contact Information for Business Card

Name: Dov Strommen
Title: "President & CEO"
Address: 31 Harlow Ln, Bexmoor, NJ 07813
Company Phone number: 800-463-5918
email: dovstrommen@petalquarry.example
website: www.petalquarry.example

Requirements
Should not have
• No black backgrounds

```html
<!DOCTYPE html>
<html lang="en">
<head>
<meta charset="utf-8">
<title>Petal Quarry Business Card</title>
<link rel="stylesheet" href="https://fonts.googleapis.com/css2?family=Questrial&display=swap">
<style>
  :root {
    --backdrop: #e4e4e4;
    --green-deep: #005c27;
    --green-soft: #3b7f41;
    --green-brand: #1e7a34;
    --mark-green: #2f9a3f;
    --card-white: #f7f7f7;
    --ink: #3a3a3a;
    --ink-soft: #555;
    --white: #ffffff;
    --white-soft: rgba(255,255,255,0.85);
  }
  * { margin: 0; padding: 0; box-sizing: border-box; }
  html, body {
    width: 1200px; height: 576px; overflow: hidden;
    background: var(--backdrop);
    font-family: "Questrial", "Century Gothic", sans-serif;
  }
  .canvas { position: relative; width: 1200px; height: 576px; }
  .card {
    position: absolute; top: 138px; width: 484px; height: 294px;
    border-radius: 14px;
    box-shadow: 0 3px 6px rgba(0,0,0,0.18);
  }
  .card-front {
    left: 82px;
    background: linear-gradient(180deg, var(--green-deep) 0%, var(--green-soft) 100%);
  }
  .front-mark {
    position: absolute; left: 50%; top: 70px; transform: translateX(-50%);
    width: 76px; height: 76px; border-radius: 50%;
    background: var(--white);
  }
  .front-name {
    position: absolute; left: 0; right: 0; top: 180px;
    text-align: center; color: var(--white);
    font-size: 29px; line-height: 36px; letter-spacing: 0.3px;
  }
  .front-tagline {
    position: absolute; left: 0; right: 0; top: 222px;
    text-align: center; color: var(--white-soft);
    font-size: 12px; line-height: 16px; letter-spacing: 1.5px;
  }
  .card-back { left: 602px; background: var(--card-white); }
  .back-mark {
    position: absolute; left: 62px; top: 96px;
    width: 96px; height: 96px; border-radius: 50%;
    background: var(--mark-green);
  }
  .back-details { position: absolute; left: 228px; top: 66px; }
  .company-name { color: var(--green-brand); font-size: 24px; line-height: 28px; font-weight: 400; }
  .person-name { color: var(--ink); font-size: 14px; line-height: 18px; margin-top: 4px; }
  .job-title { color: var(--ink-soft); font-size: 10.5px; line-height: 14px; }
  .contact-list { list-style: none; margin-top: 12px; }
  .contact-list li {
    display: flex; align-items: center; gap: 9px;
    color: var(--ink); font-size: 13px; line-height: 18px;
  }
  .contact-list svg { width: 11px; height: 11px; fill: var(--green-brand); flex: none; }
  .contact-list .address { margin-top: 1px; }
</style>
</head>
<body>
<main class="canvas">
  <section class="card card-front">
    <div class="front-mark"></div>
    <p class="front-name">Petal Quarry</p>
    <p class="front-tagline">The Professional Salon Source</p>
  </section>

  <section class="card card-back">
    <div class="back-mark"></div>
    <div class="back-details">
      <h1 class="company-name">Petal Quarry</h1>
      <p class="person-name">Dov Strommen</p>
      <p class="job-title">President &amp; CEO</p>
      <ul class="contact-list">
        <li>
          <svg viewBox="0 0 12 12" aria-hidden="true"><path d="M1 4 Q6 0 11 4 L9.5 5.5 L8 4.5 L4 4.5 L2.5 5.5 Z M3 6 H9 L10 11 H2 Z"/></svg>
          800-463-5918
        </li>
        <li>
          <svg viewBox="0 0 12 12" aria-hidden="true"><path d="M0.5 2.5 H11.5 V9.5 H0.5 Z M1.5 3.5 L6 6.8 L10.5 3.5" fill="none" stroke="#1e7a34" stroke-width="1.2"/></svg>
          dovstrommen@petalquarry.example
        </li>
        <li>
          <svg viewBox="0 0 12 12" aria-hidden="true"><circle cx="6" cy="6" r="5.2" fill="none" stroke="#1e7a34" stroke-width="1.1"/><path d="M0.8 6 H11.2 M6 0.8 Q2.5 6 6 11.2 M6 0.8 Q9.5 6 6 11.2" fill="none" stroke="#1e7a34" stroke-width="1"/></svg>
          www.petalquarry.example
        </li>
        <li class="address">31 Harlow Ln, Bexmoor, NJ 07813</li>
      </ul>
    </div>
  </section>
</main>
</body>
</html>
```